E-Commerce Web Design Project - Online Designer Childrens Clothing

I currently have a website at http://qrk.example/Tm4vRa but I am not happy with the look and feel. I mainly want black and white colours as my images will have splashes of colour

I am going for a complete new look and will require the following:

1. Home page - to have categories listed on the left side bar and large scrolling images in the center (600px by 450px) with 3 static boxes equally spaced underneath (325px by 142px) so that I can change them to different links. 3 static boxes to be on the right side bar in vertical position each size (198px by 145px).

2. category pages - to have image across the width of the page for my category title page eg. Marbury's kids. category pages to have 3 products across and ability to view all or go down to the page fold.

3. product Details pages - product image to be on the left side bar. All drop down boxes to be of equal size in width and length. Other products you may like is to be removed. Please see the following links as to what I would like it to look like layout wise http://qrk.example/Wp7dGs

4. All other pages such as the Contact us, T's and C's, About Us, Ordering and Delivery etc to have the same template where I will be able to keep adding pages as I need to.

I will be transferring my services to Tillvane and will seek a web developer once the design is confirmed.

3 websites that i love are the following:
http://qrk.example/Wp7dGs
http://qrk.example/Bz2fUe
http://qrk.example/3JtYon
http://qrk.example/gumaLQ

I want my website to be sleek and modern and have a fashion magazine feel to it. the layout is to be clean with everything in proportion. I already have my logo in greyscale that I have attached it to this project.

Please let me know if you have further questions.
Updates

would love to see more designs!i have added a couple more logo files also to add.

Reason: I have now guaranteed tthis project so hopefully more designs will come through!!

I have now guranteed this project so would love to see a few more designs!!!

Reason: I need time to review all submissions and request changes if need be

Target Market(s)

women 25-45 on good disposable income who like their designer brands and love to dress their boys in them

Industry/Entity Type

Fashion

Requirements
Must have
• must be easy to navigate and not to busy. nice and sleek with a fashion magazine feel to it. want it to be more monotone in black and white as my images will add colour
Nice to have
• I love the look of the following websites.

Home Pages:
http://qrk.example/3JtYon
http://qrk.example/Bz2fUe
http://qrk.example/hRN8T4
http://qrk.example/wiDk2v
http://qrk.example/Ezm5o
http://qrk.example/xTcHoa
http://qrk.example/P3sRyd

Category Page:

Product Details Page:
http://qrk.example/Wp7dGs
http://qrk.example/NuqaWt
http://qrk.example/RfzvIm

Products details page:
http://qrk.example/G6WJ9k
http://qrk.example/Wp7dGs

Should not have
• I do not want any quirky or childlike illustrations or the colorful blue. this website is for boys clothing but it targeted at women!!

```html
<!DOCTYPE html>
<html lang="en">
<head>
<meta charset="utf-8">
<title>Wrenfield Kids Clothing</title>
<link href="https://fonts.googleapis.com/css2?family=Pathway+Gothic+One&family=Source+Sans+3:wght@400;600;700&display=swap" rel="stylesheet">
<style>
:root{
  --black:#000;
  --white:#fff;
  --band:#e5e6e8;
  --card:#dcdddf;
  --card-line:#b9babc;
  --shop-head:#7d7e80;
  --nav:#2d2d2d;
  --nav-line:#6a6a6a;
  --text:#3a3a3a;
  --muted:#555;
}
*{margin:0;padding:0;box-sizing:border-box}
html,body{width:1200px;height:1200px;overflow:hidden;background:var(--white)}
body{position:relative;font-family:"Source Sans 3",Arial,sans-serif;color:var(--text)}
.abs{position:absolute}
.head-font{font-family:"Pathway Gothic One","Arial Narrow",sans-serif;font-weight:400}

.site-header{left:0;top:0;width:1200px;height:135px;background:var(--black)}
.logo{left:168px;top:14px;width:225px;height:62px;background:var(--white);display:flex;align-items:center;justify-content:center;gap:8px}
.logo-square{width:14px;height:14px;background:#333}
.logo-name{font-size:25px;font-weight:600;color:#333;letter-spacing:1px}
.search{left:819px;top:33px;width:211px;height:29px;background:#3a3a3a;border:1px solid #6b6b6b;color:#ddd;font-size:12px;line-height:27px;padding-left:13px}
.main-nav{left:167px;top:92px;width:861px;height:28px;background:var(--nav);border:1px solid var(--nav-line);display:flex;align-items:center;padding-left:16px;color:var(--white);font-size:12.5px;font-weight:600}
.main-nav span.sep{margin:0 22px}

.band{left:0;top:135px;width:1200px;height:437px;background:var(--band)}
.shop{left:171px;top:149px;width:309px;height:413px;background:var(--white);border:1px solid #d6d6d6}
.shop-title{height:37px;background:var(--shop-head);color:var(--white);font-size:21px;padding-left:14px;line-height:37px}
.shop-list{list-style:none;padding:18px 0 0 32px}
.shop-list li{font-size:12px;color:#555;height:31.4px}
.hero{left:498px;top:147px;width:556px;height:419px;border:1px solid #cfcfcf;background:radial-gradient(ellipse at 50% 55%,#e9dcc6 0%,#d9cdb7 55%,#cdbfa5 100%)}
.hero-arrow{top:178px;width:43px;height:36px;background:rgba(245,240,232,.85);display:flex;align-items:center;justify-content:center}

.promo{top:580px;width:302px;height:133px;background:var(--card);border:1px solid var(--card-line)}
.promo h3{position:absolute;left:25px;top:14px;font-size:21px;color:#111}
.promo .name{position:absolute;left:25px;top:50px;font-size:12px;color:#222}
.promo .price{position:absolute;left:25px;top:69px;font-size:14.5px;color:#111}
.btn{position:absolute;background:var(--black);color:var(--white);font-family:"Pathway Gothic One","Arial Narrow",sans-serif;font-size:14px;line-height:21px;padding:0 6px}
.promo .btn{left:25px;top:98px}
.thumb{position:absolute;border-radius:6px}

.welcome{left:144px;top:735px;width:708px}
.welcome h2{font-size:21px;color:#111;padding-bottom:8px;border-bottom:1px solid #ddd;margin-bottom:12px}
.welcome p{font-size:11.6px;line-height:20.3px;color:var(--text);margin-bottom:20px}
.welcome b{color:#222;font-weight:700}

.side{left:869px;width:185px;background:var(--card);border:1px solid var(--card-line)}
.side h3{position:absolute;left:13px;top:8px;font-size:20px;color:#111}
.side .line{position:absolute;left:14px;font-size:11.5px;color:#222}
.side .price{position:absolute;left:14px;font-size:14px;color:#111}

.footer{left:0;top:1157px;width:1200px;height:43px;background:var(--black);color:var(--white);font-size:12px;line-height:43px;padding-left:148px}
</style>
</head>
<body>

<header class="site-header abs">
  <div class="logo abs"><span class="logo-square"></span><span class="logo-name">WRENFIELD KIDS</span></div>
  <div class="search abs">Search</div>
  <nav class="main-nav abs">
    <span>Home</span><span class="sep">|</span><span>About Us</span><span class="sep">|</span><span>Blog</span><span class="sep">|</span><span>Sizing</span><span class="sep">|</span><span>Media</span><span class="sep">|</span><span>Contact Us</span><span class="sep">|</span><span>Login</span>
  </nav>
</header>

<div class="band abs"></div>

<aside class="shop abs">
  <div class="shop-title head-font">SHOP</div>
  <ul class="shop-list">
    <li>T Shirts And Tops</li><li>Shirts And Jumpers</li><li>Pants And Shorts</li><li>Jeans</li>
    <li>Jackets and Coats</li><li>Beachwear</li><li>Sleepwear</li><li>Shoes and Socks</li>
    <li>Accessories</li><li>Bags &amp; Luggages</li><li>Gift Certificates</li>
  </ul>
</aside>

<div class="hero abs" role="img" aria-label="Slideshow photo of a boy in a vintage aviator cap and printed tee, arms raised">
  <div class="hero-arrow abs" style="left:0">
    <svg width="12" height="16" viewBox="0 0 12 16"><path d="M9 2 L3 8 L9 14" fill="none" stroke="#111" stroke-width="2.5"/></svg>
  </div>
  <div class="hero-arrow abs" style="right:0">
    <svg width="12" height="16" viewBox="0 0 12 16"><path d="M3 2 L9 8 L3 14" fill="none" stroke="#111" stroke-width="2.5"/></svg>
  </div>
</div>

<section class="promo abs" style="left:144px">
  <h3 class="head-font">T Shirts and Tops</h3>
  <div class="name">Lad&amp;Co LS Tee</div>
  <div class="price">AU$44.00</div>
  <span class="btn">more details</span>
  <div class="thumb" style="left:178px;top:12px;width:110px;height:112px;background:linear-gradient(#a9a9a9,#8f8f8f)" role="img" aria-label="Grey long sleeve tee with tiger print"></div>
</section>
<section class="promo abs" style="left:449px">
  <h3 class="head-font">Shirts And Jumpers</h3>
  <div class="name">Marbury's Kids LS Shirt</div>
  <div class="price">AU$59.95</div>
  <span class="btn">more details</span>
  <div class="thumb" style="left:200px;top:12px;width:90px;height:118px;background:linear-gradient(#f7f7f7,#e6e6e6)" role="img" aria-label="White long sleeve shirt"></div>
</section>
<section class="promo abs" style="left:753px">
  <h3 class="head-font">Pants And Shorts</h3>
  <div class="name">Ostrava Shorts</div>
  <div class="price">SALE AU$39.00</div>
  <span class="btn">more details</span>
  <div class="thumb" style="left:170px;top:12px;width:118px;height:110px;background:linear-gradient(#e9b89a,#d99a76)" role="img" aria-label="Orange plaid shorts"></div>
</section>

<main class="welcome abs">
  <h2 class="head-font">Welcome to Our Site</h2>
  <p>So your little boy is turning into a little man and you're finding it extremely difficult to find fashionable clothes to help him develop his own sense of style. You are not alone! With the multitude of kid's clothing stores all catering mainly to little girls, parents of boys in their 'tween-age' years (8 to 14 years old) obviously have their work cut out for them. Having done considerable research, I discovered that clothes in children's wear departments were either to small or clothes in men's stores were to big!! There was no inbetween!!</p>
  <p><b>Wrenfield Kids Clothing</b> is here to change all of that!! We offer a stylish collection of designer clothes specifically targeted for this age group.</p>
  <p><b>Wrenfield Kids Clothing</b> was created for the sole purpose of providing boys with the latest fashions. We believe young men deserve to have as much choice as girls! We stock well known Australian and International Brands such as Pinecrest, Ostrava, Marbury's Kids, Tovimo, Ridgeline Denim, Ember &amp; Ash and many more! There are heaps of styles to choose from such as T-Shirts and Jeans to cool Shoes and funky PJ's!</p>
  <p>Please enjoy shopping at Wrenfield Kids Clothing and do not hesitate to contact us at info@wrenfieldkids.example should you require further assistance.</p>
</main>

<section class="side abs" style="top:722px;height:135px">
  <h3 class="head-font">Jeans</h3>
  <div class="line" style="top:48px">Ridgeline Denim</div>
  <div class="line" style="top:68px">Roll Tab Jeans</div>
  <div class="thumb" style="left:118px;top:38px;width:58px;height:88px;background:linear-gradient(#8fb0d0,#5f86ad)" role="img" aria-label="Blue denim jeans"></div>
  <div class="price" style="top:92px">SALE AU$30.00</div>
  <span class="btn" style="left:15px;top:114px">more details</span>
</section>
<section class="side abs" style="top:868px;height:136px">
  <h3 class="head-font">Jackets and Coats</h3>
  <div class="line" style="top:43px">Ridgeline Denim BMX Biker Jacket</div>
  <div class="price" style="top:60px">AU$64.95</div>
  <div class="thumb" style="left:22px;top:84px;width:110px;height:44px;background:linear-gradient(#3b4150,#242833)" role="img" aria-label="Dark denim biker jacket"></div>
  <span class="btn" style="right:0;top:114px">more details</span>
</section>
<section class="side abs" style="top:1016px;height:135px">
  <h3 class="head-font">Beachwear</h3>
  <div class="line" style="top:43px">Pinecrest Bucket Hat</div>
  <div class="price" style="top:62px">SALE AU$17.00</div>
  <div class="thumb" style="left:38px;top:86px;width:100px;height:44px;background:linear-gradient(#9fcf8a,#6ea85a)" role="img" aria-label="Green floral bucket hat"></div>
  <span class="btn" style="right:0;top:112px">more details</span>
</section>

<footer class="footer abs">Copyrights @ 2012 Al Rights Reserved</footer>

</body>
</html>
```